Home Security Company Business Card

Looking for a eye catching business card that is non traditional and stands out but yet still looks professional. It should include all the pertinent information such as name, title, address, telephone, e-mail, website address should definitely stand out and then finally the logo.

Target Market(s)

Residential and Commercial accounts mostly upscale accounts

Industry/Entity Type

Security

Contact Information for Business Card

Name
Title
Address
Office #
Cell #
E-mail
Website

Font styles to use
Serif
Sans Serif

Requirements
Must have
• Logo, two sided color configuration
Nice to have
• You decide
Should not have
• There really aren't any.

```html
<!DOCTYPE html>
<html lang="en">
<head>
<meta charset="utf-8">
<title>Ironvale Protection Group – Business Card</title>
<link href="https://fonts.googleapis.com/css2?family=Cinzel:wght@600&family=Open+Sans:wght@400;600;700&display=swap" rel="stylesheet">
<style>
  :root {
    --backdrop: #ece8e4;
    --maroon: #7a1218;
    --maroon-deep: #55090e;
    --maroon-light: #a3262d;
    --gold: #e0a52a;
    --gold-light: #f4cf6a;
    --paper: #ffffff;
    --ink-name: #8a2a2e;
  }
  * { margin: 0; padding: 0; box-sizing: border-box; }
  html, body { width: 1200px; height: 913px; overflow: hidden; }
  body {
    background: var(--backdrop);
    display: flex;
    align-items: center;
    justify-content: center;
    gap: 60px;
    font-family: "Open Sans", Arial, sans-serif;
  }
  .card {
    position: relative;
    width: 520px;
    height: 300px;
    border-radius: 18px;
    overflow: hidden;
    box-shadow: 0 10px 28px rgba(60, 20, 10, 0.25);
  }
  .card-front { background: var(--paper); }
  .card-front .wave { position: absolute; inset: 0; width: 100%; height: 100%; }

  .brand {
    font-family: "Cinzel", Georgia, serif;
    font-weight: 600;
    color: var(--maroon);
    display: flex;
    align-items: center;
    gap: 10px;
    line-height: 1.1;
  }
  .brand-dot {
    width: 30px; height: 30px; border-radius: 50%;
    background: var(--gold);
    flex: none;
  }
  .card-front .brand {
    position: absolute; left: 30px; top: 110px;
    font-size: 15px; width: 210px;
  }

  .holder { position: absolute; left: 262px; top: 32px; }
  .holder-name { font-size: 22px; font-weight: 700; color: var(--ink-name); }
  .holder-title { font-size: 13px; color: var(--gold); margin-top: -2px; }

  .contacts { position: absolute; left: 262px; top: 90px; list-style: none; }
  .contacts li {
    display: flex; align-items: center; gap: 8px;
    font-size: 12.5px; color: #3a2a2a; line-height: 20px;
    white-space: nowrap;
  }
  .contacts svg { width: 12px; height: 12px; fill: var(--gold); flex: none; }

  .address {
    position: absolute; right: 34px; bottom: 22px;
    font-size: 13.5px; color: var(--paper); letter-spacing: 0.2px;
    white-space: nowrap;
  }

  .card-back {
    background: radial-gradient(circle at 65% 20%, var(--maroon-light) 0%, var(--maroon) 45%, var(--maroon-deep) 100%);
  }
  .card-back .brand {
    position: absolute; left: 50%; top: 112px; transform: translateX(-50%);
    font-size: 24px; color: var(--gold-light); white-space: nowrap;
  }
  .card-back .brand-dot { width: 40px; height: 40px; }
  .website {
    position: absolute; left: 0; right: 0; top: 214px;
    text-align: center; font-size: 15px; font-weight: 600; color: var(--gold);
  }
</style>
</head>
<body>

<section class="card card-front" aria-label="Business card front">
  <svg class="wave" viewBox="0 0 520 300" preserveAspectRatio="none" aria-hidden="true">
    <path d="M0,228 C150,262 300,250 390,210 C450,184 490,180 520,178 L520,300 L0,300 Z" fill="var(--maroon)"/>
    <path d="M0,220 C150,254 298,242 388,202 C448,176 490,170 520,168 L520,178 C490,180 450,184 390,210 C300,250 150,262 0,228 Z" fill="var(--gold)"/>
  </svg>

  <div class="brand"><span class="brand-dot"></span><span>Ironvale Protection Group</span></div>

  <div class="holder">
    <p class="holder-name">Daniel Hartwell</p>
    <p class="holder-title">Owner</p>
  </div>

  <ul class="contacts">
    <li><svg viewBox="0 0 12 12"><path d="M1 4 Q6 0 11 4 L9.5 6 L7.5 5 L7.5 4 Q6 3.4 4.5 4 L4.5 5 L2.5 6 Z M2.5 7 H9.5 V11 H2.5 Z"/></svg>+330 5182-4417</li>
    <li><svg viewBox="0 0 12 12"><path d="M2.5 1 L4.5 1 L5.5 3.5 L4.2 4.6 Q5.2 6.8 7.4 7.8 L8.5 6.5 L11 7.5 L11 9.5 Q11 11 9.5 11 Q1 10 1 2.5 Q1 1 2.5 1 Z"/></svg>+3304716-20583</li>
    <li><svg viewBox="0 0 12 12"><path d="M1 2.5 H11 V9.5 H1 Z M1.8 3.3 L6 6.4 L10.2 3.3" fill="none" stroke="var(--gold)" stroke-width="1.3"/></svg>info@danielhartwellmail.com</li>
  </ul>

  <p class="address">742 Larkspur Avenue Aurora, Illinois 60506</p>
</section>

<section class="card card-back" aria-label="Business card back">
  <div class="brand"><span class="brand-dot"></span><span>Ironvale Protection Group</span></div>
  <p class="website">www.ironvaleprotectiongroup.com</p>
</section>

</body>
</html>
```